Very basic draft completed. Need someone to apply their creative magic

I am building a new website for my business and looking for a designer to assist me on a part-time basis.

My business is a booking site for classes and lessons. It is essentially a directory service, and needs to conform to a standard web-layout that is easy to navigate and familiar to users (i.e. nothing to creative). The function and structure i have adopted is common amongst sites like zulk, hotel booking services, etc.

The first task on my list is to develop the main page. I have already compiled a draft of the first page using Fireworks (see attached) and am looking for someone to cast their creative magic to this draft while maintaining the general layout of the page. After the main page is developed, I will be looking for the same designer to assist with the rest of the site.

Design wise, I'd like to go for a slightly retro feel
By this I mean a moderately modern page with a spark of retro here and there. If you look at my draft you'll notice that I've used regular font for most text, and retro/old-school fonts for surburb names.

I happy for you to suggest colours, but regular page elements such as web links need to remain standard (i.e links = blue) so that they are familiar and identifiable to my users.

Other points:
1) I don't want the page to be too dark (dark headings, images and borders are fine, but I'd like to maintain white or light backgrounds)

2) Positioning: The Body should be centred, with the Header and Footer extending across the hole screen (as illustrated in my draft)

3) I'm happy if the design includes images from photostock libraries.The Silhoute picture for my draft were choosen because there are hundreds of them, and I can regularly change them on the site - keeping it fresh and new. I'd be very happy if the design incorporate images that could also be place often using photo stock images (i.e. happy to keep silhoutes, but leave it to you to decide what looks best)

Note: I'm happy for you to "copy" art work from any photo stock site, and I will pay for the full quality images when the design is selected.

4) The page Footer needs a lot of attention. It will contain standard Footer links/elements.

5) You are free to do anything to the Header section. It needs to have login/register elements

I'm happy to provide further comments, or review other sites/work to help direct design work.

Hi All,

I've updated the project brief, eliminating many of the requirements and giving you the freedom with design submissions, etc. I've also added the $20 payment for submissions. 
Cheers,
Corbin

Reason: I'm away on holiday and will review your submissions and provide feedback when I get back.

```html
<!DOCTYPE html>
<html lang="en">
<head>
<meta charset="utf-8">
<title>Out &amp; About – Courses &amp; Activities</title>
<link href="https://fonts.googleapis.com/css2?family=Open+Sans:wght@400;600;700;800&display=swap" rel="stylesheet">
<style>
  :root {
    --ink: #1f1f1f;
    --bar: #3c3a3b;
    --bar-dark: #2c2a2b;
    --panel: #f4f4f4;
    --panel-line: #dedede;
    --page: #ffffff;
    --accent: #e3064f;
    --muted: #8c8c8c;
    --field: #e6e6e6;
    --footer: #000000;
    --white: #ffffff;
  }
  * { box-sizing: border-box; margin: 0; padding: 0; }
  html, body { width: 1200px; height: 958px; overflow: hidden; }
  body {
    position: relative;
    background: var(--page);
    font-family: "Open Sans", Arial, sans-serif;
    color: var(--ink);
  }
  .abs { position: absolute; }

  /* header */
  .top-rule { left: 0; top: 0; width: 1200px; height: 4px; background: var(--bar); }
  .login-panel {
    left: 827px; top: 0; width: 373px; height: 52px;
    background: linear-gradient(#4a4849, var(--bar-dark));
    border-bottom-left-radius: 8px;
  }
  .field {
    position: absolute; height: 23px; background: var(--field);
    border: 1px solid #bdbdbd; font-size: 13px; font-style: italic;
    color: #777; padding: 2px 14px;
  }
  .login-user { left: 29px; top: 13px; width: 116px; }
  .login-pass { left: 155px; top: 13px; width: 115px; }
  .login-btn {
    position: absolute; left: 279px; top: 13px; width: 71px; height: 23px;
    border-radius: 12px; background: linear-gradient(#8a8a8a, #4e4e4e);
    color: var(--white); font-size: 13px; text-align: center; line-height: 22px;
    border: 1px solid #9a9a9a;
  }
  .brand { left: 34px; top: 40px; display: flex; align-items: center; gap: 14px; }
  .brand-mark { width: 44px; height: 44px; background: #c8283e; border-radius: 4px; }
  .brand-name { font-size: 46px; font-weight: 800; color: var(--bar); letter-spacing: -1px; line-height: 1; }
  .location-rule { left: 846px; top: 70px; width: 354px; height: 1px; background: #e4e4e4; }
  .location-label { left: 865px; top: 87px; font-size: 16px; color: #444; }
  .location-select {
    left: 946px; top: 83px; width: 228px; height: 30px; border: 1px solid #c9c9c9;
    border-radius: 3px; background: #fbfbfb; font-size: 14px; padding: 5px 22px; color: #333;
  }
  .location-select .arrows { position: absolute; right: 0; top: 0; width: 22px; height: 28px; border-left: 1px solid #c9c9c9; }

  /* search bar */
  .search-bar { left: 0; top: 124px; width: 1200px; height: 62px; background: linear-gradient(#4a4849, var(--bar)); }
  .search-bar .lbl { position: absolute; color: #eaeaea; font-size: 14px; }
  .search-box {
    position: absolute; left: 34px; top: 15px; width: 156px; height: 29px; background: var(--field);
    border-radius: 3px; font-size: 14px; font-style: italic; color: #555; padding: 5px 14px;
  }
  .search-box svg { position: absolute; right: 8px; top: 6px; }
  .divider { position: absolute; top: 14px; width: 1px; height: 32px; background: #222; box-shadow: 1px 0 0 #5a5a5a; }
  .date-field { position: absolute; top: 15px; width: 85px; height: 25px; background: var(--field); border: 1px solid #aaa; }
  .cal { position: absolute; top: 15px; }
  .day { position: absolute; display: flex; align-items: center; gap: 8px; color: #ddd; font-size: 11px; }
  .box { width: 11px; height: 11px; border: 1px solid #666; background: #3a3a3a; }
  .time-select {
    position: absolute; left: 936px; top: 18px; width: 160px; height: 24px; background: var(--field);
    border: 1px solid #aaa; font-size: 11px; color: #444; padding: 4px 14px;
  }
  .time-select .drop { position: absolute; right: 0; top: 0; width: 23px; height: 22px; background: #111; }
  .filter-btn {
    position: absolute; left: 1110px; top: 18px; width: 86px; height: 24px; border-radius: 12px;
    background: linear-gradient(#9a9a9a, #5a5a5a); color: var(--white); font-size: 13px;
    text-align: center; line-height: 23px; border: 1px solid #aaa;
  }
  .close-btn { position: absolute; left: 1180px; top: 2px; width: 17px; height: 17px; background: #ddd; border: 1px solid #888; }

  /* sidebar */
  .panel { background: var(--panel); border-radius: 8px; }
  .panel-head {
    height: 36px; background: var(--bar); color: #eee; font-size: 15px;
    border-radius: 8px 8px 0 0; padding: 7px 31px;
  }
  .explore { left: 14px; top: 204px; width: 274px; height: 390px; }
  .cat-list { list-style: none; padding: 12px 0 0 32px; }
  .cat-list li { height: 36px; font-size: 15px; display: flex; align-items: center; gap: 12px; }
  .plus { width: 13px; height: 13px; border-radius: 50%; background: #333; position: relative; }
  .plus::before, .plus::after { content: ""; position: absolute; background: var(--white); }
  .plus::before { left: 3px; top: 6px; width: 7px; height: 1px; }
  .plus::after { left: 6px; top: 3px; width: 1px; height: 7px; }
  .refine { left: 14px; top: 618px; width: 274px; height: 222px; }
  .refine .panel-head { padding: 6px 26px; height: 30px; font-size: 14px; }
  .refine-label { position: absolute; left: 22px; font-size: 15px; font-weight: 700; }
  .refine-label span { font-size: 12px; font-weight: 400; color: #666; }
  .slider { position: absolute; left: 47px; width: 183px; height: 7px; border-radius: 4px; background: linear-gradient(#c9c9c9, #7a7a7a); }
  .knob { position: absolute; top: -5px; width: 17px; height: 17px; border-radius: 50%; background: var(--accent); border: 3px solid #ddd; box-shadow: 0 0 2px #555; }

  /* listing */
  .list-head {
    left: 304px; top: 204px; width: 878px; height: 36px; background: var(--bar);
    border-radius: 8px; color: #eee; font-size: 15px;
  }
  .list-head span { position: absolute; top: 7px; }
  .card { position: absolute; left: 304px; width: 878px; height: 139px; background: var(--panel); border: 1px solid var(--panel-line); }
  .thumb { position: absolute; left: 13px; top: 13px; width: 91px; height: 91px; border: 3px solid #ddd; }
  .course-title { position: absolute; left: 125px; top: 6px; font-size: 15px; font-weight: 400; color: var(--accent); }
  .course-text {
    position: absolute; left: 125px; top: 28px; width: 472px; font-size: 12.2px;
    line-height: 19.2px; text-align: justify; hyphens: auto;
  }
  .schedule { position: absolute; left: 633px; top: 4px; list-style: none; font-size: 12px; line-height: 18px; color: var(--muted); }
  .place { position: absolute; left: 710px; top: 22px; width: 96px; text-align: center; font-size: 12px; }
  .map-icon { position: absolute; left: 733px; top: 58px; }
  .price { position: absolute; left: 810px; top: 24px; width: 62px; text-align: center; font-size: 26px; font-weight: 600; line-height: 1.1; }
  .price small { display: block; font-size: 12px; font-weight: 400; line-height: 18px; margin-top: 6px; }

  /* footer */
  .footer { left: 0; top: 848px; width: 1200px; height: 110px; background: var(--footer); z-index: 2; }
  .foot-col { position: absolute; top: 17px; list-style: none; font-size: 15px; line-height: 20px; color: var(--white); }
  .foot-col .foot-title { color: var(--accent); }
</style>
</head>
<body>
  <div class="abs top-rule"></div>

  <header>
    <div class="abs brand">
      <span class="brand-mark"></span>
      <span class="brand-name">Out &amp; About</span>
    </div>

    <form class="abs login-panel">
      <div class="field login-user">User Name</div>
      <div class="field login-pass">Password</div>
      <div class="login-btn">Login</div>
    </form>

    <div class="abs location-rule"></div>
    <div class="abs location-label">Location</div>
    <div class="abs location-select">Prahran
      <svg class="arrows" viewBox="0 0 22 28"><path d="M7 12l4-4 4 4zM7 16l4 4 4-4z" fill="#555"/></svg>
    </div>
  </header>

  <section class="abs search-bar">
    <div class="search-box">Search
      <svg width="17" height="17" viewBox="0 0 17 17"><circle cx="7" cy="7" r="5" fill="none" stroke="#333" stroke-width="2"/><path d="M11 11l5 5" stroke="#333" stroke-width="2.5"/></svg>
    </div>
    <div class="divider" style="left:245px"></div>
    <span class="lbl" style="left:304px;top:20px">Date From</span>
    <div class="date-field" style="left:376px"></div>
    <svg class="cal" style="left:467px" width="29" height="29" viewBox="0 0 29 29"><rect x="1" y="2" width="27" height="26" rx="2" fill="#fff" stroke="#d21f2b" stroke-width="2"/><rect x="1" y="2" width="27" height="8" fill="#d21f2b"/><text x="17" y="23" font-size="9" font-family="Open Sans, sans-serif" fill="#333">21</text></svg>
    <span class="lbl" style="left:518px;top:20px">To</span>
    <div class="date-field" style="left:542px"></div>
    <svg class="cal" style="left:634px" width="29" height="29" viewBox="0 0 29 29"><rect x="1" y="2" width="27" height="26" rx="2" fill="#fff" stroke="#d21f2b" stroke-width="2"/><rect x="1" y="2" width="27" height="8" fill="#d21f2b"/><text x="17" y="23" font-size="9" font-family="Open Sans, sans-serif" fill="#333">21</text></svg>
    <div class="divider" style="left:688px"></div>

    <label class="day" style="left:702px;top:10px"><span class="box" style="background:#666"></span>Mon</label>
    <label class="day" style="left:760px;top:10px"><span class="box"></span>Tue</label>
    <label class="day" style="left:815px;top:10px"><span class="box"></span>Wed</label>
    <label class="day" style="left:864px;top:10px"><span class="box"></span>Thu</label>
    <label class="day" style="left:702px;top:32px"><span class="box"></span>Fri</label>
    <label class="day" style="left:760px;top:32px"><span class="box"></span>Sat</label>
    <label class="day" style="left:815px;top:32px"><span class="box"></span>Sun</label>
    <label class="day" style="left:864px;top:32px"><span class="box"></span>All</label>

    <div class="time-select">Any Time of Day
      <svg class="drop" viewBox="0 0 23 22"><circle cx="11.5" cy="11" r="7" fill="#ddd"/><path d="M8 9l3.5 4 3.5-4" stroke="#111" stroke-width="2" fill="none"/></svg>
    </div>
    <div class="filter-btn">Filter</div>
    <svg class="close-btn" viewBox="0 0 17 17"><path d="M4 4l9 9M13 4l-9 9" stroke="#333" stroke-width="2"/></svg>
  </section>

  <aside>
    <nav class="abs panel explore">
      <div class="panel-head">Exolore Courseses &amp; Activities</div>
      <ul class="cat-list">
        <li><span class="plus"></span>Visual Arts (32)</li>
        <li><span class="plus"></span>Cooking (14)</li>
        <li><span class="plus"></span>Health / Fitnes (19)</li>
        <li><span class="plus"></span>Home / Life (12)</li>
        <li><span class="plus"></span>Languages (31)</li>
        <li><span class="plus"></span>Performing Arts (28)</li>
        <li><span class="plus"></span>Professional (5)</li>
        <li><span class="plus"></span>Tech/ Internet (8)</li>
        <li><span class="plus"></span>Arts and Sciences (9)</li>
      </ul>
    </nav>

    <section class="abs panel refine">
      <div class="panel-head">Refine Search ( recommented)</div>
      <div class="refine-label" style="top:44px">Age: <span>18 yrs+</span></div>
      <div class="slider" style="top:79px"><span class="knob" style="left:45px"></span></div>
      <div class="refine-label" style="top:122px">Max Price: <span>$50</span></div>
      <div class="slider" style="top:167px"><span class="knob" style="left:45px"></span></div>
    </section>
  </aside>

  <main>
    <div class="abs list-head">
      <span style="left:10px">Showing: All Courses &amp; Activities</span>
      <span style="left:619px">Schedule</span>
      <span style="left:727px">Location</span>
      <span style="left:820px">Price</span>
    </div>

    <article class="card" style="top:258px">
      <div class="thumb" role="img" aria-label="Couple dancing salsa" style="background:linear-gradient(135deg,#5a3a22,#b0703a 55%,#d9a062)"></div>
      <h3 class="course-title">Salsa Patterns</h3>
      <p class="course-text">The standard chunk of Lorem Ipsum used since the 1500s is reproduced below for those interested. Sections 1.10.32 and 1.10.33 from "de Finibus Bonorum et Malorum" by Tullian are also reproduced in their exact original form, accompanied by English versions from the 1914 translation by J. Ashby.</p>
      <ul class="schedule"><li>M 6pm</li><li>T &nbsp;6px</li><li>W &nbsp;5px, 7pm</li><li>T &nbsp;-</li><li>F &nbsp;- 7px</li><li>S &nbsp;-</li><li>S &nbsp;-</li></ul>
      <div class="place">South Bank</div>
      <svg class="map-icon" width="46" height="46" viewBox="0 0 46 46"><rect x="1" y="1" width="44" height="44" rx="8" fill="#e2e2e2" stroke="#999" stroke-width="2"/><path d="M8 30L38 14M14 8l16 32" stroke="#fff" stroke-width="4"/><path d="M30 18a4 4 0 1 1 8 0c0 4-4 8-4 8s-4-4-4-8z" fill="#d21f2b"/></svg>
      <div class="price">$15<small>Single<br>Session</small></div>
    </article>

    <article class="card" style="top:407px">
      <div class="thumb" role="img" aria-label="Tango dancers performing" style="background:linear-gradient(135deg,#1b1414,#5a2a2a 60%,#2a1e1e)"></div>
      <h3 class="course-title">Argenine Tango - Intermediate</h3>
      <p class="course-text">The standard chunk of Lorem Ipsum used since the 1500s is reproduced below for those interested. Sections 1.10.32 and 1.10.33 from "de Finibus Bonorum et Malorum" by Tullian are also reproduced in their exact original form, accompanied by English versions from the 1914 translation by J. Ashby.</p>
      <ul class="schedule"><li>M 6pm</li><li>T &nbsp;6px</li><li>W &nbsp;5px, 7pm</li><li>T &nbsp;-</li><li>F &nbsp;- 7px</li><li>S &nbsp;-</li><li>S &nbsp;-</li></ul>
      <div class="place">South Bank</div>
      <svg class="map-icon" width="46" height="46" viewBox="0 0 46 46"><rect x="1" y="1" width="44" height="44" rx="8" fill="#e2e2e2" stroke="#999" stroke-width="2"/><path d="M8 30L38 14M14 8l16 32" stroke="#fff" stroke-width="4"/><path d="M30 18a4 4 0 1 1 8 0c0 4-4 8-4 8s-4-4-4-8z" fill="#d21f2b"/></svg>
      <div class="price">$60<small>Single<br>Session</small></div>
    </article>

    <article class="card" style="top:555px">
      <div class="thumb" role="img" aria-label="Women exercising on mats" style="background:linear-gradient(135deg,#c9b38a,#8c7a62 55%,#3a3330)"></div>
      <h3 class="course-title">Kick Your Booty Mat</h3>
      <p class="course-text">The standard chunk of Lorem Ipsum used since the 1500s is reproduced below for those interested. Sections 1.10.32 and 1.10.33 from "de Finibus Bonorum et Malorum" by Tullian are also reproduced in their exact original form, accompanied by English versions from the 1914 translation by J. Ashby.</p>
      <ul class="schedule"><li>M 6pm</li><li>T &nbsp;6px</li><li>W &nbsp;5px, 7pm</li><li>T &nbsp;-</li><li>F &nbsp;- 7px</li><li>S &nbsp;-</li><li>S &nbsp;-</li></ul>
      <div class="place">South Bank</div>
      <svg class="map-icon" width="46" height="46" viewBox="0 0 46 46"><rect x="1" y="1" width="44" height="44" rx="8" fill="#e2e2e2" stroke="#999" stroke-width="2"/><path d="M8 30L38 14M14 8l16 32" stroke="#fff" stroke-width="4"/><path d="M30 18a4 4 0 1 1 8 0c0 4-4 8-4 8s-4-4-4-8z" fill="#d21f2b"/></svg>
      <div class="price">$54<small>Single<br>Session</small></div>
    </article>

    <article class="card" style="top:716px">
      <div class="thumb" role="img" aria-label="Ballroom dancer in gown on stage" style="background:linear-gradient(135deg,#0e1230,#2c2f6a 55%,#8a86b8)"></div>
      <h3 class="course-title">Ballroom Dancing for Beginers</h3>
      <p class="course-text">The standard chunk of Lorem Ipsum used since the 1500s is reproduced below for those interested. Sections 1.10.32 and 1.10.33 from "de Finibus Bonorum et Malorum" by Tullian are also reproduced in their exact original form, accompanied by English versions from the 1914 translation by J. Ashby.</p>
      <ul class="schedule"><li>M 6pm</li><li>T &nbsp;6px</li><li>W &nbsp;5px, 7pm</li><li>T &nbsp;-</li><li>F &nbsp;- 7px</li><li>S &nbsp;-</li><li>S &nbsp;-</li></ul>
      <div class="place">South Bank</div>
      <svg class="map-icon" width="46" height="46" viewBox="0 0 46 46"><rect x="1" y="1" width="44" height="44" rx="8" fill="#e2e2e2" stroke="#999" stroke-width="2"/><path d="M8 30L38 14M14 8l16 32" stroke="#fff" stroke-width="4"/><path d="M30 18a4 4 0 1 1 8 0c0 4-4 8-4 8s-4-4-4-8z" fill="#d21f2b"/></svg>
      <div class="price">$83<small>Single<br>Session</small></div>
    </article>
  </main>

  <footer class="abs footer">
    <ul class="foot-col" style="left:304px"><li class="foot-title">Contact Us</li></ul>
    <ul class="foot-col" style="left:476px"><li class="foot-title">Customers</li><li>Register</li><li>Login</li><li>Manage Booking</li></ul>
    <ul class="foot-col" style="left:622px"><li class="foot-title">Business</li><li>&nbsp;Register</li><li>&nbsp;List a Class or Activity</li></ul>
  </footer>
</body>
</html>
```